Firm Stationery Design

I need a design for stationery, including: Stationery First Page, Stationery Second Sheet, Envelope, Mailing Label for Flat Envelopes, and Business Cards

```html
<!DOCTYPE html>
<html lang="en">
<head>
<meta charset="utf-8">
<title>Harlow Law LLC — Stationery</title>
<link href="https://fonts.googleapis.com/css2?family=Montserrat:wght@400;500;700;800&display=swap" rel="stylesheet">
<style>
  :root {
    --ink: #1c1c1c;
    --orange: #f59f1e;
    --paper: #ffffff;
    --backdrop: #ece6dc;
    --muted: #3a3a3a;
  }
  * { box-sizing: border-box; margin: 0; padding: 0; }
  html, body { width: 1200px; height: 884px; overflow: hidden; }
  body {
    position: relative;
    background: var(--backdrop);
    font-family: "Montserrat", sans-serif;
    color: var(--ink);
  }
  .sheet {
    position: absolute;
    background: var(--paper);
    box-shadow: 0 3px 8px rgba(0,0,0,.22);
    overflow: hidden;
  }
  .footer-band {
    position: absolute; left: 0; right: 0; bottom: 0;
    display: flex; gap: 2px; background: var(--paper);
  }
  .footer-band .band-dark { background: var(--ink); }
  .footer-band .band-accent { background: var(--orange); flex: 1; }

  /* masthead: name lockup followed by address, laid out side by side */
  .masthead { position: absolute; display: flex; align-items: flex-start; }

  /* name lockup: plain square above the firm name */
  .lockup {
    display: flex; flex-direction: column; align-items: center;
    font-weight: 800; color: var(--ink); line-height: 1.1;
    letter-spacing: .03em; text-align: center; white-space: nowrap; flex: none;
  }
  .lockup .mark-square { background: var(--orange); flex: none; }

  .address { border-left: 1px solid var(--orange); color: var(--muted); line-height: 1.45; white-space: nowrap; }

  /* note card large */
  .note-large { left: 60px; top: 109px; width: 323px; height: 242px; }
  .note-large .masthead { left: 22px; top: 21px; gap: 9px; }
  .note-large .lockup { font-size: 11px; gap: 6px; }
  .note-large .lockup .mark-square { width: 22px; height: 22px; }
  .note-large .address { margin-top: 0; padding: 7px 0 7px 7px; font-size: 8.5px; }
  .note-large .footer-band { height: 14px; }
  .note-large .band-dark { width: 248px; }

  /* note card small */
  .note-small { left: 425px; top: 109px; width: 179px; height: 239px; }
  .note-small .masthead { left: 14px; top: 14px; gap: 6px; }
  .note-small .lockup { font-size: 7px; gap: 4px; }
  .note-small .lockup .mark-square { width: 15px; height: 15px; }
  .note-small .address { padding: 2px 0 4px 5px; font-size: 6px; }
  .note-small .footer-band { height: 10px; }
  .note-small .band-dark { width: 143px; }

  /* envelope back */
  .envelope { left: 60px; top: 422px; width: 364px; height: 160px; }
  .envelope .flap { position: absolute; left: 0; top: 0; width: 364px; height: 70px; }
  .envelope .lockup { position: absolute; left: 0; right: 0; top: 10px; font-size: 7.5px; gap: 3px; }
  .envelope .lockup .mark-square { width: 14px; height: 14px; }

  /* mailing label */
  .label { left: 60px; top: 618px; width: 363px; height: 158px; }
  .label .masthead { left: 14px; top: 14px; gap: 7px; }
  .label .lockup { font-size: 7.5px; gap: 4px; }
  .label .lockup .mark-square { width: 16px; height: 16px; }
  .label .address { padding: 3px 0 5px 8px; font-size: 6px; }
  .label .footer-band { height: 12px; }
  .label .band-dark { width: 299px; }

  /* business cards */
  .card { border-radius: 10px; }
  .card-front { left: 486px; top: 413px; width: 287px; height: 163px; }
  .card-front .lockup { position: absolute; left: 0; right: 0; top: 24px; font-size: 20px; gap: 10px; }
  .card-front .lockup .mark-square { width: 46px; height: 46px; }

  .card-back { left: 486px; top: 612px; width: 287px; height: 163px; }
  .card-back .lockup { position: absolute; left: 28px; top: 40px; font-size: 13px; gap: 7px; }
  .card-back .lockup .mark-square { width: 32px; height: 32px; }
  .card-back .details { position: absolute; left: 136px; top: 33px; padding-left: 11px; border-left: 1px solid var(--orange); font-size: 8px; line-height: 1.45; color: var(--muted); }
  .card-back .holder-name { color: var(--orange); font-weight: 700; font-size: 12px; letter-spacing: .02em; line-height: 1.2; }
  .card-back .holder-role { margin-bottom: 6px; }
  .card-back .holder-address { margin-bottom: 6px; }
  .card-back .footer-band { height: 12px; }
  .card-back .band-dark { width: 217px; }

  .contact-list { list-style: none; }
  .contact-list li { display: flex; align-items: center; gap: 3px; }
  .contact-list svg { flex: none; fill: var(--orange); }

  /* letterhead */
  .letterhead { left: 814px; top: 193px; width: 327px; height: 463px; }
  .letterhead .lockup { position: absolute; left: 30px; top: 18px; font-size: 11px; gap: 6px; }
  .letterhead .lockup .mark-square { width: 26px; height: 26px; }
  .letterhead .address { position: absolute; left: 213px; top: 27px; padding: 1px 0 1px 8px; font-size: 6.2px; line-height: 1.35; }
  .letterhead .contact-list { margin-top: 3px; }
  .letterhead .recipient { position: absolute; left: 30px; top: 122px; font-size: 6.2px; line-height: 1.5; color: var(--muted); }
  .letterhead .recipient small { display: block; font-size: 4.6px; line-height: 1.75; }
  .letterhead .letter-body { position: absolute; left: 30px; top: 181px; width: 266px; font-size: 4.4px; line-height: 1.85; color: var(--muted); text-align: justify; }
  .letterhead .letter-body p + p { margin-top: 7px; }
  .letterhead .sign-off { position: absolute; left: 30px; top: 359px; font-size: 5px; color: var(--muted); }
  .letterhead .signature { display: block; width: 40px; height: 9px; margin: 4px 0 3px; background: linear-gradient(90deg, #2a2a2a, #555); border-radius: 4px; opacity: .75; }
  .letterhead .signer { font-size: 6px; }
  .letterhead .footer-band { height: 13px; }
  .letterhead .band-dark { width: 259px; }
</style>
</head>
<body>

  <!-- Correspondence card, landscape -->
  <section class="sheet note-large">
    <div class="masthead">
      <div class="lockup"><span class="mark-square"></span><span>HARLOW<br>LAW LLC</span></div>
      <div class="address">Your address, City<br>State, Zip 1234</div>
    </div>
    <div class="footer-band"><span class="band-dark"></span><span class="band-accent"></span></div>
  </section>

  <!-- Correspondence card, portrait -->
  <section class="sheet note-small">
    <div class="masthead">
      <div class="lockup"><span class="mark-square"></span><span>HARLOW<br>LAW LLC</span></div>
      <div class="address">Your address, City<br>State, Zip 1234</div>
    </div>
    <div class="footer-band"><span class="band-dark"></span><span class="band-accent"></span></div>
  </section>

  <!-- Envelope, back with flap -->
  <section class="sheet envelope">
    <svg class="flap" viewBox="0 0 364 70" aria-hidden="true">
      <defs>
        <filter id="flap-shadow" x="-5%" y="-20%" width="110%" height="160%">
          <feDropShadow dx="0" dy="5" stdDeviation="5" flood-color="#000" flood-opacity=".18"/>
        </filter>
      </defs>
      <path d="M0 0 H364 L352 44 Q346 57 330 57 H34 Q18 57 12 44 Z" fill="#fff" filter="url(#flap-shadow)"/>
    </svg>
    <div class="lockup"><span class="mark-square"></span><span>HARLOW<br>LAW LLC</span></div>
  </section>

  <!-- Mailing label -->
  <section class="sheet label">
    <div class="masthead">
      <div class="lockup"><span class="mark-square"></span><span>HARLOW<br>LAW LLC</span></div>
      <div class="address">Your address, City<br>State, Zip 1234</div>
    </div>
    <div class="footer-band"><span class="band-dark"></span><span class="band-accent"></span></div>
  </section>

  <!-- Business card, front -->
  <section class="sheet card card-front">
    <div class="lockup"><span class="mark-square"></span><span>HARLOW<br>LAW LLC</span></div>
  </section>

  <!-- Business card, back -->
  <section class="sheet card card-back">
    <div class="lockup"><span class="mark-square"></span><span>HARLOW<br>LAW LLC</span></div>
    <div class="details">
      <div class="holder-name">DANIEL REYES</div>
      <div class="holder-role">Managing Director</div>
      <div class="holder-address">Your address, City<br>State, Zip 1234</div>
      <ul class="contact-list">
        <li><svg width="6" height="6" viewBox="0 0 10 10"><path d="M1 3 Q5 0 9 3 L8 5 L6.5 4 V3.5 H3.5 V4 L2 5 Z M2 6 H8 V9 H2 Z"/></svg>123 456 789</li>
        <li><svg width="6" height="6" viewBox="0 0 10 10"><path d="M0 2 H10 V8 H0 Z"/><path d="M0 2 L5 5.5 L10 2" fill="none" stroke="#fff" stroke-width="1"/></svg>info@harlowlawllc.com</li>
        <li><svg width="6" height="6" viewBox="0 0 10 10"><circle cx="5" cy="5" r="4.5"/><path d="M0.5 5 H9.5 M5 0.5 V9.5" stroke="#fff" stroke-width=".8"/></svg>www.harlowlawllc.com</li>
      </ul>
    </div>
    <div class="footer-band"><span class="band-dark"></span><span class="band-accent"></span></div>
  </section>

  <!-- Letterhead, first page -->
  <section class="sheet letterhead">
    <div class="lockup"><span class="mark-square"></span><span>HARLOW<br>LAW LLC</span></div>
    <div class="address">
      Your address, City<br>State, Zip 1234
      <ul class="contact-list">
        <li><svg width="5" height="5" viewBox="0 0 10 10"><path d="M1 3 Q5 0 9 3 L8 5 L6.5 4 V3.5 H3.5 V4 L2 5 Z M2 6 H8 V9 H2 Z"/></svg>123 456 789</li>
        <li><svg width="5" height="5" viewBox="0 0 10 10"><path d="M0 2 H10 V8 H0 Z"/><path d="M0 2 L5 5.5 L10 2" fill="none" stroke="#fff" stroke-width="1"/></svg>info@harlowlawllc.com</li>
        <li><svg width="5" height="5" viewBox="0 0 10 10"><circle cx="5" cy="5" r="4.5"/><path d="M0.5 5 H9.5 M5 0.5 V9.5" stroke="#fff" stroke-width=".8"/></svg>www.harlowlawllc.com</li>
      </ul>
    </div>

    <div class="recipient">
      MAREN CASTELL
      <small>Chief Executive Officer<br>City/State, Zip Code</small>
    </div>

    <div class="letter-body">
      <p>Proin gravida nibh vel velit auctor aliquet. Aenean sollicitudin, lorem quis bibendum auctor, nisi elit consequat ipsum, nec sagittis sem nibh id elit. Duis sed odio sit amet nibh vulputate cursus a sit amet mauris. Morbi accumsan ipsum velit. Nam nec tellus a odio tincidunt auctor a ornare odio. Sed non mauris vitae erat consequat auctor eu in elit. Class aptent taciti sociosqu ad litora torquent per conubia nostra.</p>
      <p>Nullam ac urna eu felis dapibus condimentum sit amet a augue. Sed non neque elit. Sed ut imperdiet nisi. Proin condimentum fermentum nunc. Etiam pharetra, erat sed fermentum feugiat, velit mauris egestas quam, ut aliquam massa nisl quis neque. Suspendisse in orci enim.</p>
      <p>Mauris in erat justo. Duis sed odio sit amet nibh vulputate cursus. Class aptent taciti sociosqu ad litora torquent. Nam nec tellus a odio tincidunt auctor a ornare odio. Etiam pharetra erat sed fermentum feugiat, velit mauris egestas quam, ut aliquam massa nisl quis neque.</p>
    </div>

    <div class="sign-off">
      Sincerely,
      <span class="signature" role="img" aria-label="Handwritten signature"></span>
      <span class="signer">Tomas Avery</span>
    </div>

    <div class="footer-band"><span class="band-dark"></span><span class="band-accent"></span></div>
  </section>

</body>
</html>
```